Bright Campus Network Sign

We need a sign that can be displayed on the front fence of schools that shows that will proudly proclaim that the school is an BCN School
The Bright Campus Network is one of the world's leading organisations suppprting schools to become innovative and adaptive organisations.
Updates

The signs are being cut from 2400x1200 boards Signs are 55x40 can be either orientation

Target Market(s)

Parents and educators

Industry/Entity Type

Education

Requirements
Must have
• Edgy. Professional. NOT conservative. Crisp.
• Colours and styles to match existing logos
Nice to have
• The Marlowe Advisory logo is just for reference as it is the parent company. ONLY want reference to BCN.
• Keep it simple. Not too busy. Elegant but edgy
Should not have
• No symbols to do with traditioanl education. NO PENS, MORTAR BOARDS, BOOKS

```html
<!DOCTYPE html>
<html lang="en">
<head>
<meta charset="UTF-8">
<title>Bright Campus Network Sign</title>
<link rel="stylesheet" href="https://fonts.googleapis.com/css2?family=EB+Garamond:wght@500&family=Tinos:wght@700&display=swap">
<style>
  :root {
    --purple: #532c7f;
    --green: #5c7d37;
    --paper: #fdfdfd;
    --soft-purple: #b9a6d0;
    --soft-green: #b7c8a0;
  }
  html, body {
    margin: 0;
    padding: 0;
    overflow: hidden;
    background: var(--paper);
  }
  .sign {
    position: relative;
    width: 1200px;
    height: 800px;
    background: var(--paper);
    overflow: hidden;
  }
  .tree-art {
    position: absolute;
    inset: 0;
    width: 1200px;
    height: 800px;
  }
  .org-name {
    position: absolute;
    left: 96px;
    top: 286px;
    margin: 0;
    font-family: "Tinos", "Times New Roman", serif;
    font-weight: 700;
    font-size: 40px;
    line-height: 79px;
    letter-spacing: 0.05em;
    color: var(--purple);
    text-transform: uppercase;
  }
  .tagline {
    position: absolute;
    left: 96px;
    top: 462px;
    margin: 0;
    font-family: "EB Garamond", Garamond, serif;
    font-weight: 500;
    font-size: 74px;
    line-height: 80px;
    letter-spacing: 0.01em;
    text-transform: uppercase;
  }
  .tagline span { display: block; }
  .tagline .accent-green { color: var(--green); }
  .tagline .accent-purple { color: var(--purple); }
</style>
</head>
<body>
  <main class="sign">
    <svg class="tree-art" viewBox="0 0 1200 800" role="img" aria-label="Decorative tree of leaves and raised-arm figures in purple and green, spreading across the top and right side">
      <defs>
        <linearGradient id="foliage" x1="0" y1="0" x2="1" y2="1">
          <stop offset="0" stop-color="var(--soft-purple)"/>
          <stop offset="1" stop-color="var(--soft-green)"/>
        </linearGradient>
      </defs>
      <path d="M270 0 H1200 V800 H640 C650 600 690 420 660 300 C620 230 520 210 470 220 C400 230 330 200 290 130 C270 80 265 30 270 0 Z" fill="url(#foliage)"/>
    </svg>

    <h1 class="org-name">Bright Campus<br>Network</h1>

    <p class="tagline">
      <span class="accent-green">Transforming</span>
      <span class="accent-green">Schools</span>
      <span class="accent-purple">Together</span>
    </p>
  </main>
</body>
</html>
```